Orbit Voltix VR is the name of our project, We are a Virtual Reality Theme park

We need a web page and logo that is sharp and exciting, and futuristic that people would want to have on a tee shirt.. We like teal -black- silver colour. Customers will be able to book on line- we will have Free Roam VR experiences , Trundla(treadmills), Stand alone VR stations and VR Simulator rides.

Orbit Voltix VR

```html
<!DOCTYPE html>
<html lang="en">
<head>
<meta charset="utf-8">
<title>Orbit Voltix VR – Home page, light and dark</title>
<link href="https://fonts.googleapis.com/css2?family=Oswald:wght@500;600&family=Open+Sans:ital,wght@0,400;0,600;0,700;1,600&display=swap" rel="stylesheet">
<style>
:root{
  --teal:#1f9c9b;
  --teal-dark:#17807f;
  --ink:#151515;
  --black:#111111;
  --footer:#161616;
  --white:#ffffff;
  --grey:#6b6b6b;
  --line:#d9d9d9;
  --canvas:#f3f3f3;
  --head:'Oswald',sans-serif;
  --body:'Open Sans',sans-serif;
}
*{box-sizing:border-box;margin:0;padding:0}
html,body{width:955px;height:1200px;overflow:hidden;background:var(--canvas)}
.stage{position:absolute;left:0;top:0;width:1194px;height:1500px;transform:scale(.8);transform-origin:0 0}
.page{position:absolute;top:118px;width:443px;height:1264px;background:var(--white);overflow:hidden;font-family:var(--body);color:var(--ink);box-shadow:0 2px 10px rgba(0,0,0,.08)}
.page--light{left:107px}
.page--dark{left:645px}
.abs{position:absolute}

/* hero */
.hero{left:0;top:0;width:443px;height:268px;background:
  radial-gradient(circle at 76% 34%,#e9e6ff 0 6%,#8b5cf6 18%,rgba(60,40,200,.0) 34%),
  linear-gradient(180deg,#2a2fb8 0%,#1f2a9a 45%,#6a2d9e 72%,#c0428f 88%,#3b2b6b 100%)}
.brand{left:40px;top:18px;font-family:var(--head);font-weight:600;font-size:14px;color:var(--white);letter-spacing:.2px}
.nav{left:192px;top:22px;display:flex;gap:8px;font-family:var(--head);font-weight:500;font-size:6.5px;color:var(--white);align-items:center}
.nav .is-active{color:#5fd6d4}
.hero-title{left:40px;top:82px;font-family:var(--head);font-weight:600;font-size:24px;color:var(--white)}
.hero-sub{left:41px;top:118px;font-size:9px;color:var(--white)}
.btn{display:flex;align-items:center;justify-content:center;border-radius:12px;font-family:var(--body);font-weight:700;font-size:6px;letter-spacing:.2px}
.btn--solid{background:var(--teal);color:var(--white)}
.btn--outline{border:1px solid var(--teal);color:var(--teal);background:transparent}
.btn--black{background:#0d0d0d;color:var(--white)}
.hero-btn{left:41px;top:141px;width:70px;height:24px}
.slide-arrow{top:122px;width:14px;height:20px;background:rgba(0,0,0,.55)}

/* welcome */
.welcome-bg{left:0;top:268px;width:443px;height:996px}
.welcome-title{left:40px;top:296px;font-family:var(--head);font-weight:600;font-size:18px;line-height:24px}
.welcome-copy{left:40px;top:352px;width:180px;font-size:5.2px;line-height:10.6px;color:var(--grey)}
.welcome-btn{left:40px;top:417px;width:59px;height:21px}
.portrait{left:245px;top:274px;width:158px;height:158px;border-radius:50%;background:radial-gradient(circle at 40% 35%,#e0607a,#6a3a78 55%,#233a6a)}
.divider{left:40px;top:474px;width:362px;height:1px;background:var(--line)}
.section-title{left:0;width:443px;text-align:center;font-family:var(--head);font-weight:600;font-size:17px}

/* games */
.band{left:0;top:600px;width:443px;height:282px}
.card{width:113px;height:150px;background:var(--white);box-shadow:0 1px 4px rgba(0,0,0,.2);text-align:center}
.card-img{position:absolute;left:2px;top:2px;width:109px;height:74px}
.card-title{position:absolute;left:0;right:0;top:84px;font-family:var(--head);font-weight:500;font-size:8.2px;color:var(--ink)}
.card-text{position:absolute;left:10px;right:10px;top:100px;font-size:4.6px;line-height:9.8px;color:var(--grey)}
.card-more{position:absolute;left:0;right:0;top:134px;font-weight:700;font-size:5px;color:var(--teal)}
.chev{top:589px;font-size:14px;color:#888;font-family:var(--body)}

/* testimonials */
.quote{left:80px;top:765px;width:284px;text-align:center;font-style:italic;font-weight:600;font-size:7.6px;line-height:14.6px;color:var(--white)}
.quote-name{left:0;top:821px;width:443px;text-align:center;font-weight:700;font-size:6.5px;color:var(--white)}
.avatar{left:201px;top:850px;width:40px;height:40px;border-radius:50%;background:radial-gradient(circle at 50% 40%,#c99a7e,#5b4136);border:2px solid var(--white)}

/* booking */
.field{height:18px;background:var(--white);border:1px solid #cfcfcf;font-size:4.8px;color:#777;padding:5px 6px}
.submit{left:194px;top:1072px;width:55px;height:20px;font-size:6px}
.skyline{left:0;top:1000px;width:443px;height:138px}

/* footer */
.footer{left:0;top:1138px;width:443px;height:126px;background:var(--footer);color:#d6d6d6;text-align:center}
.social{position:absolute;top:34px;width:17px;height:17px;border-radius:50%;border:1px solid #cfcfcf}
.foot-line{position:absolute;left:0;right:0;font-size:4.9px}

/* dark variant */
.page--dark .welcome-bg{background:var(--black)}
.page--dark .welcome-title,.page--dark .section-title{color:var(--white)}
.page--dark .welcome-copy{color:#bdbdbd}
.page--dark .divider{background:#333}
</style>
</head>
<body>
<div class="stage">

<!-- ============ light page ============ -->
<section class="page page--light">
  <div class="abs hero" role="img" aria-label="Night photo of a neon ferris wheel and theme park"></div>
  <div class="abs brand">ORBIT VOLTIX VR</div>
  <nav class="abs nav"><span class="is-active">HOME</span><span>ABOUT US</span><span>SERVICES</span><span>GAMES</span><span>NEWS</span><span>GALLERY</span><span>CONTACT</span>
    <svg width="7" height="7" viewBox="0 0 10 10"><circle cx="4" cy="4" r="3" fill="none" stroke="#fff" stroke-width="1.5"/><line x1="6.3" y1="6.3" x2="9" y2="9" stroke="#fff" stroke-width="1.5"/></svg></nav>
  <h1 class="abs hero-title">ORBIT VOLTIX VR</h1>
  <p class="abs hero-sub">We are a Virtual Reality Theme park.</p>
  <div class="abs btn btn--solid hero-btn">BOOK ONLINE</div>
  <div class="abs slide-arrow" style="left:0"><svg width="14" height="20"><path d="M8 6 L5 10 L8 14" fill="none" stroke="#fff" stroke-width="1.3"/></svg></div>
  <div class="abs slide-arrow" style="left:429px"><svg width="14" height="20"><path d="M6 6 L9 10 L6 14" fill="none" stroke="#fff" stroke-width="1.3"/></svg></div>

  <div class="abs welcome-bg"></div>
  <svg class="abs" style="left:0;top:250px" width="443" height="200"><path d="M270 20 A95 95 0 0 1 378 22" fill="none" stroke="var(--teal)" stroke-width="1.3"/><path d="M250 110 A80 80 0 0 0 400 135" fill="none" stroke="var(--teal)" stroke-width="1.3"/><path d="M262 18 Q323 -8 384 18 Z" fill="#fff"/></svg>
  <h2 class="abs welcome-title">WELCOME TO<br>ORBIT VOLTIX VR</h2>
  <p class="abs welcome-copy">Nam libero tempore, cum soluta nobis est eligendi optio cumque nihil impedit quo minus id quod maxime placeat facere possimus, omnis voluptas assumenda est, omnis dolor repellendus. Temporibus autem quibusdam et aut officiis debitis aut rerum necessitatibus saepe eveniet ut voluptates repudiandae sint et molestiae.</p>
  <div class="abs btn btn--outline welcome-btn">READ MORE</div>
  <div class="abs portrait" role="img" aria-label="Photo of a visitor wearing a VR headset"></div>
  <div class="abs divider"></div>
  <h2 class="abs section-title" style="top:504px">GAMES WE PROVIDE</h2>

  <svg class="abs band" viewBox="0 0 443 282" width="443" height="282">
    <path d="M0 42 Q221 -8 443 42 L443 280 L0 280 Z" fill="var(--teal)"/>
    <path d="M0 32 Q221 -18 443 32" fill="none" stroke="var(--teal)" stroke-width="1"/>
    <rect x="0" y="80" width="443" height="200" fill="#27a9a7" opacity=".35"/>
  </svg>
  <span class="abs chev" style="left:17px">&#8249;</span><span class="abs chev" style="left:419px">&#8250;</span>
  <article class="abs card" style="left:41px;top:548px"><div class="card-img" role="img" aria-label="Photo of a player in a free roam VR arena" style="background:linear-gradient(135deg,#1a1a2a,#6a1f3a 70%,#c0304a)"></div><h3 class="card-title">Roam VR experiences</h3><p class="card-text">At vero eos et accusamus et iusto odio dignissimos ducimus qui blanditiis praesenti voluptatum dele</p><span class="card-more">READ MORE</span></article>
  <article class="abs card" style="left:165px;top:548px"><div class="card-img" role="img" aria-label="Photo of stand alone VR stations" style="background:linear-gradient(135deg,#c9a24a,#5a6a8a 50%,#2d3550)"></div><h3 class="card-title">Stand alone VR stations</h3><p class="card-text">At vero eos et accusamus et iusto odio dignissimos ducimus qui blanditiis praesenti voluptatum dele</p><span class="card-more">READ MORE</span></article>
  <article class="abs card" style="left:288px;top:548px"><div class="card-img" role="img" aria-label="Photo of a VR simulator ride" style="background:linear-gradient(135deg,#6fa0b8,#8d8a8a 50%,#d0a13a)"></div><h3 class="card-title">VR Simulator rides</h3><p class="card-text">At vero eos et accusamus et iusto odio dignissimos ducimus qui blanditiis praesenti voluptatum dele</p><span class="card-more">READ MORE</span></article>

  <h2 class="abs section-title" style="top:732px;color:#fff">TESTIMONIALS</h2>
  <svg class="abs" style="left:31px;top:778px" width="381" height="18"><circle cx="9" cy="9" r="8" fill="none" stroke="#fff"/><path d="M10.5 5.5 L7 9 L10.5 12.5" fill="none" stroke="#fff"/><circle cx="372" cy="9" r="8" fill="none" stroke="#fff"/><path d="M370.5 5.5 L374 9 L370.5 12.5" fill="none" stroke="#fff"/></svg>
  <p class="abs quote">“ Nam libero tempore, cum soluta nobis est eligendi optio cumque nihil im pedit quo minus id quod maxime placeat facere possimus, omnis voluptas assumenda est, omnis dolor repellen oribus autem quibusd ”</p>
  <p class="abs quote-name">JOHN DOE</p>
  <svg class="abs" style="left:196px;top:870px" width="50" height="28"><path d="M3 14 A22 22 0 0 0 47 14" fill="none" stroke="var(--teal)" stroke-width="1.2"/></svg>
  <div class="abs avatar" role="img" aria-label="Customer portrait"></div>

  <div class="abs skyline" role="img" aria-label="Faint roller coaster and ferris wheel silhouette" style="background:linear-gradient(180deg,rgba(230,230,230,0) 0%,#ececec 60%,#e2e2e2 100%)"></div>
  <h2 class="abs section-title" style="top:928px">BOOK ONLINE</h2>
  <div class="abs field" style="left:78px;top:966px;width:139px">Name</div>
  <div class="abs field" style="left:224px;top:966px;width:139px">Surname</div>
  <div class="abs field" style="left:78px;top:991px;width:139px">Email address</div>
  <div class="abs field" style="left:224px;top:991px;width:139px">Phone number</div>
  <div class="abs field" style="left:78px;top:1016px;width:285px;height:33px">Message</div>
  <div class="abs btn btn--solid submit">SUBMIT</div>

  <footer class="abs footer">
    <span class="social" style="left:180px"></span><span class="social" style="left:202px"></span><span class="social" style="left:224px"></span><span class="social" style="left:246px"></span>
    <p class="foot-line" style="top:66px">&#9679; 118-240 Harbor Row, Lakeview, SK S0K 1A0, Canada &nbsp;|&nbsp; &#9742; 1 800 555 0199 &nbsp;|&nbsp; &#9993; hello@orbitvoltixvr.com</p>
    <p class="foot-line" style="top:83px">Help &nbsp; | &nbsp; FAQ &nbsp; | &nbsp; Support &nbsp; | &nbsp; Sitemap &nbsp; | &nbsp; Terms Of Use &nbsp; | &nbsp; Privacy Statement</p>
    <p class="foot-line" style="top:99px">Orbit Voltix VR © 2019 All rights reserved.</p>
  </footer>
</section>

<!-- ============ dark page ============ -->
<section class="page page--dark">
  <div class="abs hero" role="img" aria-label="Night photo of a neon ferris wheel and theme park"></div>
  <div class="abs brand">ORBIT VOLTIX VR</div>
  <nav class="abs nav"><span class="is-active">HOME</span><span>ABOUT US</span><span>SERVICES</span><span>GAMES</span><span>NEWS</span><span>GALLERY</span><span>CONTACT</span>
    <svg width="7" height="7" viewBox="0 0 10 10"><circle cx="4" cy="4" r="3" fill="none" stroke="#fff" stroke-width="1.5"/><line x1="6.3" y1="6.3" x2="9" y2="9" stroke="#fff" stroke-width="1.5"/></svg></nav>
  <h1 class="abs hero-title">ORBIT VOLTIX VR</h1>
  <p class="abs hero-sub">We are a Virtual Reality Theme park.</p>
  <div class="abs btn btn--solid hero-btn">BOOK ONLINE</div>
  <div class="abs slide-arrow" style="left:0"><svg width="14" height="20"><path d="M8 6 L5 10 L8 14" fill="none" stroke="#fff" stroke-width="1.3"/></svg></div>
  <div class="abs slide-arrow" style="left:429px"><svg width="14" height="20"><path d="M6 6 L9 10 L6 14" fill="none" stroke="#fff" stroke-width="1.3"/></svg></div>

  <div class="abs welcome-bg"></div>
  <svg class="abs" style="left:0;top:250px" width="443" height="200"><path d="M262 18 Q323 -8 384 18 Z" fill="var(--black)"/><path d="M270 20 A95 95 0 0 1 378 22" fill="none" stroke="var(--teal)" stroke-width="1.3"/><path d="M250 110 A80 80 0 0 0 400 135" fill="none" stroke="var(--teal)" stroke-width="1.3"/></svg>
  <h2 class="abs welcome-title">WELCOME TO<br>ORBIT VOLTIX VR</h2>
  <p class="abs welcome-copy">Nam libero tempore, cum soluta nobis est eligendi optio cumque nihil impedit quo minus id quod maxime placeat facere possimus, omnis voluptas assumenda est, omnis dolor repellendus. Temporibus autem quibusdam et aut officiis debitis aut rerum necessitatibus saepe eveniet ut voluptates repudiandae sint et molestiae.</p>
  <div class="abs btn btn--outline welcome-btn">READ MORE</div>
  <div class="abs portrait" role="img" aria-label="Photo of a visitor wearing a VR headset"></div>
  <div class="abs divider"></div>
  <h2 class="abs section-title" style="top:504px">GAMES WE PROVIDE</h2>

  <svg class="abs band" viewBox="0 0 443 282" width="443" height="282">
    <path d="M0 42 Q221 -8 443 42 L443 280 L0 280 Z" fill="#2a2a2a"/>
    <path d="M0 32 Q221 -18 443 32" fill="none" stroke="var(--teal)" stroke-width="1"/>
    <rect x="0" y="80" width="443" height="200" fill="#3a3a3a" opacity=".45"/>
  </svg>
  <span class="abs chev" style="left:17px;color:#666">&#8249;</span><span class="abs chev" style="left:419px;color:#666">&#8250;</span>
  <article class="abs card" style="left:41px;top:548px"><div class="card-img" role="img" aria-label="Photo of a player in a free roam VR arena" style="background:linear-gradient(135deg,#1a1a2a,#6a1f3a 70%,#c0304a)"></div><h3 class="card-title">Roam VR experiences</h3><p class="card-text">At vero eos et accusamus et iusto odio dignissimos ducimus qui blanditiis praesenti voluptatum dele</p><span class="card-more">READ MORE</span></article>
  <article class="abs card" style="left:165px;top:548px"><div class="card-img" role="img" aria-label="Photo of stand alone VR stations" style="background:linear-gradient(135deg,#c9a24a,#5a6a8a 50%,#2d3550)"></div><h3 class="card-title">Stand alone VR stations</h3><p class="card-text">At vero eos et accusamus et iusto odio dignissimos ducimus qui blanditiis praesenti voluptatum dele</p><span class="card-more">READ MORE</span></article>
  <article class="abs card" style="left:288px;top:548px"><div class="card-img" role="img" aria-label="Photo of a VR simulator ride" style="background:linear-gradient(135deg,#6fa0b8,#8d8a8a 50%,#d0a13a)"></div><h3 class="card-title">VR Simulator rides</h3><p class="card-text">At vero eos et accusamus et iusto odio dignissimos ducimus qui blanditiis praesenti voluptatum dele</p><span class="card-more">READ MORE</span></article>

  <h2 class="abs section-title" style="top:732px">TESTIMONIALS</h2>
  <svg class="abs" style="left:31px;top:778px" width="381" height="18"><circle cx="9" cy="9" r="8" fill="none" stroke="#fff"/><path d="M10.5 5.5 L7 9 L10.5 12.5" fill="none" stroke="#fff"/><circle cx="372" cy="9" r="8" fill="none" stroke="#fff"/><path d="M370.5 5.5 L374 9 L370.5 12.5" fill="none" stroke="#fff"/></svg>
  <p class="abs quote">“ Nam libero tempore, cum soluta nobis est eligendi optio cumque nihil im pedit quo minus id quod maxime placeat facere possimus, omnis voluptas assumenda est, omnis dolor repellen oribus autem quibusd ”</p>
  <p class="abs quote-name">JOHN DOE</p>

  <div class="abs" style="left:0;top:880px;width:443px;height:258px;background:var(--teal)"></div>
  <div class="abs skyline" role="img" aria-label="Roller coaster and ferris wheel silhouette" style="background:linear-gradient(180deg,rgba(23,128,127,0) 0%,var(--teal-dark) 70%,#146f6e 100%)"></div>
  <svg class="abs" style="left:196px;top:870px" width="50" height="28"><path d="M3 14 A22 22 0 0 0 47 14" fill="none" stroke="#fff" stroke-width="1.2"/></svg>
  <div class="abs avatar" role="img" aria-label="Customer portrait"></div>
  <h2 class="abs section-title" style="top:928px;color:#fff">BOOK ONLINE</h2>
  <div class="abs field" style="left:78px;top:966px;width:139px">Name</div>
  <div class="abs field" style="left:224px;top:966px;width:139px">Surname</div>
  <div class="abs field" style="left:78px;top:991px;width:139px">Email address</div>
  <div class="abs field" style="left:224px;top:991px;width:139px">Phone number</div>
  <div class="abs field" style="left:78px;top:1016px;width:285px;height:33px">Message</div>
  <div class="abs btn btn--black submit">SUBMIT</div>

  <footer class="abs footer">
    <span class="social" style="left:180px"></span><span class="social" style="left:202px"></span><span class="social" style="left:224px"></span><span class="social" style="left:246px"></span>
    <p class="foot-line" style="top:66px">&#9679; 118-240 Harbor Row, Lakeview, SK S0K 1A0, Canada &nbsp;|&nbsp; &#9742; 1 800 555 0199 &nbsp;|&nbsp; &#9993; hello@orbitvoltixvr.com</p>
    <p class="foot-line" style="top:83px">Help &nbsp; | &nbsp; FAQ &nbsp; | &nbsp; Support &nbsp; | &nbsp; Sitemap &nbsp; | &nbsp; Terms Of Use &nbsp; | &nbsp; Privacy Statement</p>
    <p class="foot-line" style="top:99px">Orbit Voltix VR © 2019 All rights reserved.</p>
  </footer>
</section>

</div>
</body>
</html>
```